Design a web site for my business - Brightline Coatings Co.

We are a family business that handles design, fabrication and installation of powder coated aluminum, stainless steel and glass products. Including handrails, privacy slat screens, electric gates and pool fencing. We are based in the Whitsundays in North Queensland and service an area from Airlie Beach to Townsville.

Target Market(s)

Domestic and commercial

Industry/Entity Type

fabrication - manufacturing

Coding

Coded - Design and coding required

Number of Pages Required

5+ page

Colors
0054AA
0677BA
7BADD7
CADEEF
E8F1F8

Requirements
Must have
• photo galleries, contact page, one page for privacy screens, balustrades, glass fencing, stainless steel handrail, powder coated aluminium handrails and pool fencing

```html
<!DOCTYPE html>
<html lang="en">
<head>
<meta charset="utf-8">
<title>Brightline Coatings Co — Aluminium &amp; Glass, Whitsundays</title>
<link rel="stylesheet" href="https://fonts.googleapis.com/css2?family=Lexend+Zetta:wght@800;900&family=Poppins:wght@400;500;600;700&display=swap">
<style>
:root{
  --blue-deep:#0054AA;
  --blue:#0677BA;
  --blue-mid:#7BADD7;
  --blue-pale:#CADEEF;
  --blue-mist:#E8F1F8;
  --ink:#1b1f24;
  --text:#3d4550;
  --white:#ffffff;
  --footer:#212326;
  --star:#f0a22b;
}
*{box-sizing:border-box;margin:0;padding:0}
html,body{width:1200px;height:4914px;overflow:hidden}
body{position:relative;background:var(--white);font-family:"Poppins",sans-serif;color:var(--text);font-size:11px;line-height:1.6}
.abs{position:absolute}
.display{font-family:"Lexend Zetta",sans-serif;font-weight:900;text-transform:uppercase;color:var(--ink);letter-spacing:-1px;line-height:1.05}
.eyebrow{font-size:11px;font-weight:500;color:var(--blue)}
.btn{display:inline-flex;align-items:center;justify-content:center;height:32px;padding:0 18px;border-radius:16px;font-size:10px;font-weight:600;text-decoration:none}
.btn-solid{background:var(--blue);color:var(--white)}
.btn-line{border:1.5px solid var(--blue-mid);color:var(--blue-deep);background:var(--white)}
.photo{position:absolute}

/* Hero */
.hero{position:absolute;left:0;top:0;width:1200px;height:780px;overflow:hidden}
.hero-bg{position:absolute;inset:0;background:linear-gradient(180deg,#0d2340 0%,#1d4e6e 28%,#2f6a5e 52%,#5e4a35 74%,#2a2218 100%)}
.hero-shade{position:absolute;inset:0;background:linear-gradient(90deg,rgba(8,20,40,.55) 0%,rgba(8,20,40,.1) 60%)}
.brand{position:absolute;display:flex;align-items:center;gap:8px;color:var(--white);font-weight:600;font-size:12px;letter-spacing:.5px;text-transform:uppercase}
.brand-dot{width:14px;height:14px;border-radius:50%;background:var(--blue-mid)}
.nav{position:absolute;left:400px;top:34px;display:flex;gap:22px;color:var(--white);font-size:10px;font-weight:500}
.call{position:absolute;left:797px;top:22px;display:flex;align-items:center;gap:10px;color:var(--white)}
.call-icon{width:36px;height:36px;border-radius:50%;background:rgba(255,255,255,.25);display:flex;align-items:center;justify-content:center}
.call small{display:block;font-size:10px;color:var(--blue-mid);line-height:1.2}
.call b{font-size:12px;font-weight:600}
.hero-quote{left:948px;top:27px;height:32px;padding:0 24px}
.hero-kicker{left:151px;top:257px;color:var(--white);font-size:11px;font-weight:500}
.hero h1{position:absolute;left:151px;top:280px;font-size:37px;color:var(--white);width:640px;letter-spacing:-1.5px}
.hero-lead{left:151px;top:398px;width:440px;color:var(--white);font-size:10.5px;line-height:1.6}
.hero-btns{left:151px;top:450px;display:flex;gap:8px}
.stats{left:151px;top:580px;display:flex;color:var(--white)}
.stat{width:144px}
.stat b{display:block;font-family:"Lexend Zetta",sans-serif;font-weight:900;font-size:22px;line-height:1.1;letter-spacing:-1px}
.stat span{font-size:10.5px}

/* About */
.about-photo{left:120px;top:870px;width:460px;height:360px;border-radius:220px 40px 220px 40px;background:linear-gradient(135deg,#5b6b78 0%,#a9b4bc 40%,#6d7f8c 70%,#2f3a45 100%)}
.about-rule{left:10px;top:870px;width:605px;height:3px;background:linear-gradient(90deg,#cfd4d8,#6a6f74)}
.about-text{left:636px;top:864px;width:420px}
.about-text h2{font-size:24px;margin:6px 0 12px}
.about-text p{font-size:10.5px;margin-bottom:10px}

/* Services */
.center{left:0;width:1200px;text-align:center}
.section-title{font-size:26px}
.cards{left:151px;top:1435px;display:flex;gap:5px}
.card{width:221px;height:340px;background:var(--white);box-shadow:0 6px 18px rgba(0,40,90,.12);position:relative}
.card .pic{height:168px}
.card h3{font-family:"Lexend Zetta",sans-serif;font-weight:800;font-size:12px;color:var(--ink);text-transform:uppercase;margin:36px 25px 8px;letter-spacing:-.3px}
.card p{font-size:9.5px;line-height:1.6;margin:0 25px}
.card .go{position:absolute;left:25px;bottom:-6px;width:28px;height:28px;background:var(--blue);display:flex;align-items:center;justify-content:center}

/* Process */
.process{left:0;top:1860px;width:1200px;height:580px}
.process h2{color:var(--white)}
.step-line{left:82px;top:2121px;width:986px;height:5px;background:var(--white);border-radius:3px}
.step-icon{position:absolute;top:2091px;width:64px;height:64px;border-radius:50%;border:5px solid var(--white);display:flex;align-items:center;justify-content:center}
.step-num{position:absolute;top:-12px;right:-6px;width:22px;height:22px;border-radius:50%;background:var(--white);color:var(--ink);font-size:9px;font-weight:600;display:flex;align-items:center;justify-content:center}
.step{position:absolute;top:2176px;width:215px;color:var(--white)}
.step h3{font-family:"Lexend Zetta",sans-serif;font-weight:800;font-size:12px;text-transform:uppercase;letter-spacing:-.3px;margin-bottom:8px}
.step p{font-size:9.5px;line-height:1.6;color:#e3eef8}

/* Projects */
.tile{position:absolute}
.tile-note{left:467px;top:2572px;width:265px;height:250px;background:rgba(123,173,215,.88);color:var(--white);text-align:center;padding-top:106px}
.tile-note h4{font-family:"Poppins",sans-serif;font-weight:600;font-size:15px;text-transform:uppercase;letter-spacing:.3px}
.tile-note p{font-size:10px;width:170px;margin:4px auto 0;line-height:1.6}

/* Service area */
.area-text{left:151px;top:3390px;width:430px}
.area-text h2{font-size:27px;margin:6px 0 14px}
.area-text p{font-size:10.5px;margin-bottom:10px}

/* Testimonials */
.quote-card{position:absolute;top:3844px;width:295px;height:220px;background:linear-gradient(180deg,var(--blue-mist) 0%,var(--white) 100%);border:1.5px solid var(--blue-pale);padding:50px 36px 0}
.stars{color:var(--star);font-size:12px;letter-spacing:1px;margin-bottom:10px}
.quote-card p{font-size:10px;line-height:1.7;color:var(--text)}
.quote-card .who{margin-top:4px;font-size:10px}
.quote-card .who b{color:var(--ink)}
.dots{left:584px;top:4078px;display:flex;gap:8px}
.dots i{width:6px;height:6px;border-radius:50%;background:var(--blue-pale)}
.dots i.on{background:var(--blue)}

/* CTA */
.cta-kicker{left:151px;top:4276px;color:var(--white);font-size:11px;font-weight:500}
.cta h2{position:absolute;left:151px;top:4296px;font-size:25px;color:var(--white)}
.cta-lead{left:151px;top:4330px;width:540px;color:#e3eef8;font-size:10px}
.cta-btn{left:918px;top:4293px;background:var(--white);color:var(--blue-deep);height:30px}

/* Footer */
.footer-about{left:151px;top:4623px;width:290px;color:#b9bec4;font-size:10px;line-height:1.7}
.fcol{position:absolute;top:4508px}
.fcol h4{font-family:"Lexend Zetta",sans-serif;font-weight:800;font-size:12px;color:var(--white);text-transform:uppercase;letter-spacing:-.3px}
.fcol h4::after{content:"";display:block;width:26px;height:2px;background:var(--blue);margin:6px 0 14px}
.fcol li{list-style:none;color:#b9bec4;font-size:10px;line-height:22px}
.contact-strip{left:151px;top:4780px;width:898px;display:flex;justify-content:space-between}
.contact-item{display:flex;align-items:center;gap:16px;color:var(--white);font-size:10px}
.contact-item .ic{width:36px;height:36px;border-radius:50%;background:#2f3237;display:flex;align-items:center;justify-content:center}
.contact-item small{display:block;font-weight:600;font-size:10px}
.contact-item b{font-weight:600}
.footer-rule{left:151px;top:4858px;width:898px;height:1px;background:#3a3d42}
.legal{top:4870px;color:#9aa0a6;font-size:10px}
.to-top{left:1104px;top:4824px;width:28px;height:28px;border-radius:50%;background:var(--white);display:flex;align-items:center;justify-content:center}
</style>
</head>
<body>

<!-- Hero -->
<header class="hero">
  <div class="hero-bg" role="img" aria-label="Photo of a timber and powder coated aluminium boardwalk railing along a tropical waterfront at dusk"></div>
  <div class="hero-shade"></div>
  <div class="brand" style="left:151px;top:66px"><span class="brand-dot"></span>Brightline Coatings Co</div>
  <nav class="nav">
    <span>&#8962;</span><span>Home</span><span>About</span><span>Services &#709;</span><span>Projects</span><span>Service Area</span><span>Contact</span>
  </nav>
  <div class="call">
    <span class="call-icon"><svg width="14" height="14" viewBox="0 0 24 24" fill="#fff"><path d="M6.6 10.8a15.1 15.1 0 0 0 6.6 6.6l2.2-2.2c.3-.3.7-.4 1-.2 1.1.4 2.3.6 3.6.6.6 0 1 .4 1 1V20c0 .6-.4 1-1 1A17 17 0 0 1 3 4c0-.6.4-1 1-1h3.5c.6 0 1 .4 1 1 0 1.3.2 2.5.6 3.6.1.3 0 .7-.2 1z"/></svg></span>
    <div><small>Call Us:</small><b>07 4900 1234</b></div>
  </div>
  <a class="btn btn-solid abs hero-quote">Get a Quote</a>
  <div class="abs hero-kicker">Family Owned &amp; Operated — Whitsundays</div>
  <h1 class="display">Crafting Excellence in Aluminium &amp; Glass</h1>
  <p class="abs hero-lead">Design, fabrication &amp; installation of powder coated aluminium, stainless steel &amp; glass products across the Whitsundays region — from Airlie Beach to Townsville.</p>
  <div class="abs hero-btns"><a class="btn btn-solid">Request a Free Quote</a><a class="btn" style="border:1.5px solid #fff;color:#fff">Our Services</a></div>
  <div class="abs stats">
    <div class="stat"><b>15+</b><span>Years Experience</span></div>
    <div class="stat" style="width:172px"><b>500+</b><span>Projects Completed</span></div>
    <div class="stat"><b>100%</b><span>Family Owned</span></div>
    <div class="stat"><b>24/7</b><span>Customer Support</span></div>
  </div>
  <svg class="abs" style="left:0;top:600px" width="1200" height="180" viewBox="0 0 1200 180"><path d="M0 175 C 420 168 760 150 1000 100 C 1100 80 1160 60 1200 68 L1200 180 L0 180Z" fill="#fff"/></svg>
</header>

<!-- About -->
<section>
  <div class="abs about-rule"></div>
  <div class="photo about-photo" role="img" aria-label="Photo of the fabrication workshop with metalwork and welding"></div>
  <div class="abs about-text">
    <div class="eyebrow">About Our Business</div>
    <h2 class="display">A Family Tradition of Quality Craftsmanship</h2>
    <p>We are a proud family-run business based in the heart of the Whitsundays, North Queensland. For over 15 years, we have been designing, fabricating and installing premium powder coated aluminium, stainless steel and glass products for homes and businesses throughout the region.</p>
    <p>From concept to completion, our hands-on approach ensures every project meets the highest standards. We treat every job — big or small — with the same care and attention to detail that you'd expect from a family business.</p>
    <a class="btn btn-line" style="margin-top:6px">Get in touch with our family</a>
  </div>
</section>

<!-- Services -->
<section>
  <div class="abs center eyebrow" style="top:1288px">What We Do</div>
  <h2 class="abs center display section-title" style="top:1310px">Premium Aluminium &amp;<br>Glass Solutions</h2>
  <p class="abs" style="left:390px;top:1378px;width:420px;text-align:center;font-size:10.5px">From design to installation, we deliver complete solutions for residential and commercial properties across the Whitsundays region.</p>
  <div class="abs cards">
    <article class="card">
      <div class="pic" role="img" aria-label="Photo of a stainless steel handrail on a timber walkway" style="background:linear-gradient(160deg,#9aa59a,#6e5a48 60%,#4b5a3f)"></div>
      <h3>Handrails</h3>
      <p>Stylish and durable powder coated aluminium and stainless steel handrails for staircases, balconies, walkways and ramps. Custom designs to suit any architecture.</p>
      <span class="go"><svg width="10" height="10" viewBox="0 0 10 10"><path d="M1 5h7M5 2l3 3-3 3" stroke="#fff" stroke-width="1.4" fill="none"/></svg></span>
    </article>
    <article class="card">
      <div class="pic" role="img" aria-label="Photo of a white aluminium privacy slat fence" style="background:linear-gradient(180deg,#1f5fb0,#8fb2d6 45%,#d9d6cf)"></div>
      <h3>Privacy Slat</h3>
      <p>Modern aluminium slat screens offering privacy without compromising on style. Perfect for patios, fences, carports and outdoor entertaining areas.</p>
      <span class="go"><svg width="10" height="10" viewBox="0 0 10 10"><path d="M1 5h7M5 2l3 3-3 3" stroke="#fff" stroke-width="1.4" fill="none"/></svg></span>
    </article>
    <article class="card">
      <div class="pic" role="img" aria-label="Photo of a grey electric sliding gate in front of a modern house" style="background:linear-gradient(180deg,#c6d2dc,#7c848a 55%,#4a5a3e)"></div>
      <h3>Electric Gates</h3>
      <p>Secure and convenient automatic electric gates crafted from premium aluminium. Smooth operation, robust construction and smart access control options.</p>
      <span class="go"><svg width="10" height="10" viewBox="0 0 10 10"><path d="M1 5h7M5 2l3 3-3 3" stroke="#fff" stroke-width="1.4" fill="none"/></svg></span>
    </article>
    <article class="card">
      <div class="pic" role="img" aria-label="Photo of frameless glass pool fencing beside a garden" style="background:linear-gradient(180deg,#6f8a62,#a8b8a6 50%,#5c7356)"></div>
      <h3>Pool Fencing</h3>
      <p>AS1926.1 compliant pool fencing that combines safety with elegance. Frameless glass, semi-frameless and aluminium options to suit any pool area.</p>
      <span class="go"><svg width="10" height="10" viewBox="0 0 10 10"><path d="M1 5h7M5 2l3 3-3 3" stroke="#fff" stroke-width="1.4" fill="none"/></svg></span>
    </article>
  </div>
</section>

<!-- Process -->
<section class="abs process">
  <svg class="abs" style="left:0;top:0" width="1200" height="580" viewBox="0 0 1200 580"><path d="M0 110 C 300 60 700 10 1200 20 L1200 560 C 900 480 400 520 0 525Z" fill="#0a6fbb"/><path d="M0 110 C 300 60 700 10 1200 20 L1200 60 C 800 50 400 90 0 150Z" fill="#0054AA" opacity=".35"/></svg>
  <div class="abs center" style="top:142px;color:#fff;font-size:11px;font-weight:500">How It Works</div>
  <h2 class="abs center display section-title" style="top:164px;color:#fff">From First Call to Final Fit</h2>
</section>
<div class="abs step-line"></div>
<div class="step-icon" style="left:170px;background:var(--blue-deep)"><svg width="26" height="26" viewBox="0 0 24 24" fill="none" stroke="#fff" stroke-width="1.6"><circle cx="12" cy="8" r="4"/><path d="M4 21c0-4 4-6 8-6s8 2 8 6"/></svg><span class="step-num">01</span></div>
<div class="step-icon" style="left:395px;background:var(--blue-mid)"><svg width="26" height="26" viewBox="0 0 24 24" fill="none" stroke="#fff" stroke-width="1.8"><path d="M5 7h5v5H7l-2 5M14 7h5v5h-3l-2 5"/></svg><span class="step-num">02</span></div>
<div class="step-icon" style="left:626px;background:var(--blue-mid)"><svg width="26" height="26" viewBox="0 0 24 24" fill="none" stroke="#fff" stroke-width="1.6"><path d="M3 20V10l5 3V10l5 3V6h8v14z"/></svg><span class="step-num">03</span></div>
<div class="step-icon" style="left:849px;background:var(--blue-mid)"><svg width="26" height="26" viewBox="0 0 24 24" fill="none" stroke="#fff" stroke-width="1.6"><circle cx="12" cy="12" r="3"/><path d="M12 2v3M12 19v3M2 12h3M19 12h3M5 5l2 2M17 17l2 2M5 19l2-2M17 7l2-2"/></svg><span class="step-num">04</span></div>
<div class="step" style="left:176px"><h3>Consult &amp; Measure</h3><p>We visit your site anywhere between Airlie Beach and Townsville to discuss your vision, take precise measurements and assess site conditions.</p></div>
<div class="step" style="left:399px"><h3>Design &amp; Quote</h3><p>We put together a tailored design, material and colour selection with a transparent, itemised quote — no surprises later.</p></div>
<div class="step" style="left:628px"><h3>Fabricate In-House</h3><p>Your product is cut, welded, finished and powder coated in our own workshop, checked at every stage for quality.</p></div>
<div class="step" style="left:857px"><h3>Professional Install</h3><p>Our own installation crew fits your finished product on site, cleans up, and walks you through care and compliance.</p></div>

<!-- Projects -->
<section>
  <div class="abs center eyebrow" style="top:2442px">Our Work</div>
  <h2 class="abs center display section-title" style="top:2464px">Recent Projects</h2>
  <p class="abs" style="left:390px;top:2498px;width:420px;text-align:center;font-size:10.5px">Take a look at some of our recent installations across the Whitsundays, Bowen, and Townsville regions.</p>
  <div class="tile" role="img" aria-label="Photo of a glass pool fence beside clear blue water" style="left:151px;top:2554px;width:294px;height:277px;background:linear-gradient(160deg,#2fb7c9,#7fd3d9 45%,#4f8a54)"></div>
  <div class="tile" role="img" aria-label="Photo of a balcony with glass balustrade overlooking the coast" style="left:151px;top:2839px;width:294px;height:364px;background:linear-gradient(180deg,#dfe6ea,#cfc5b4 55%,#a78660)"></div>
  <div class="tile" role="img" aria-label="Photo of an automatic entry gate at a home" style="left:452px;top:2554px;width:294px;height:355px;background:linear-gradient(180deg,#5c6a78,#8f99a0 60%,#3c4148)"></div>
  <div class="tile tile-note"><h4>Automatic Entry Gates</h4><p>Custom sliding electric gate with remote access for a property in Bowen.</p></div>
  <div class="tile" role="img" aria-label="Photo of a black slatted aluminium entry portal at night" style="left:452px;top:2917px;width:294px;height:286px;background:linear-gradient(180deg,#3f6a52,#1d2126 50%,#6f7a60)"></div>
  <div class="tile" role="img" aria-label="Photo of a black staircase with frameless glass balustrade" style="left:755px;top:2554px;width:294px;height:416px;background:linear-gradient(160deg,#f0f2f3,#b8bcc0 50%,#1e2226)"></div>
  <div class="tile" role="img" aria-label="Photo of a decorative laser cut pool fence panel" style="left:755px;top:2978px;width:294px;height:225px;background:linear-gradient(160deg,#1f8fd0,#3ab0e6 50%,#8ec3d9)"></div>
  <a class="btn btn-line abs" style="left:519px;top:3225px;width:162px">Start Your Project Today</a>
</section>

<!-- Service area -->
<section>
  <div class="abs area-text">
    <div class="eyebrow">Service Area</div>
    <h2 class="display">Serving the Whitsundays &amp; Beyond</h2>
    <p>Based in the beautiful Whitsundays region, we proudly service a broad area of North Queensland — from the pristine beaches of Airlie Beach to the vibrant city of Townsville and everywhere in between.</p>
    <p>Whether you're on Hamilton Island, a coastal property in Bowen, or a rural home in Proserpine — our team is ready to bring your project to life with the same dedication and quality we're known for.</p>
  </div>
  <div class="photo" role="img" aria-label="Map of the North Queensland coast from Townsville to Gladstone with service towns marked" style="left:582px;top:3281px;width:534px;height:430px;border-radius:40px;background:radial-gradient(ellipse at 55% 50%,#eef4fa 0%,#f6f9fc 60%,#ffffff 100%)"></div>
</section>

<!-- Testimonials -->
<section>
  <div class="abs center eyebrow" style="top:3772px">Testimonials</div>
  <h2 class="abs center display section-title" style="top:3794px">What Our Clients Say</h2>
  <div class="quote-card" style="left:151px"><div class="stars">★★★★★</div><p>"The team designed and installed a frameless glass pool fence for us that looks amazing and passed certification without a hitch. Couldn't be happier."</p><p class="who"><b>Jenna K.</b> — Airlie Beach</p></div>
  <div class="quote-card" style="left:452px"><div class="stars">★★★★★</div><p>"Our new electric gate has been rock solid through two wet seasons now. Great communication from quote through to install, genuinely a family business you can trust."</p><p class="who"><b>Tom B.</b> — Airlie Beach</p></div>
  <div class="quote-card" style="left:755px"><div class="stars">★★★★★</div><p>"Powder coated privacy screens around our alfresco turned out better than we imagined. Fast turnaround and tidy tradesmen on-site."</p><p class="who"><b>Priya L.</b> — Airlie Beach</p></div>
  <div class="abs dots"><i></i><i class="on"></i><i></i></div>
</section>

<!-- CTA -->
<section class="cta">
  <svg class="abs" style="left:0;top:4180px" width="1200" height="340" viewBox="0 0 1200 340"><path d="M0 80 C 400 60 800 20 1200 0 L1200 340 L0 340Z" fill="#0a6fbb"/></svg>
  <div class="abs cta-kicker">Get In Touch</div>
  <h2 class="display">Request Your Free Quote</h2>
  <p class="abs cta-lead">Tell us a bit about your project and we'll get back to you to arrange a site visit and measure, anywhere from Airlie Beach to Townsville.</p>
  <a class="btn abs cta-btn">Request a Free Quote</a>
</section>

<!-- Footer -->
<footer>
  <svg class="abs" style="left:0;top:4390px" width="1200" height="524" viewBox="0 0 1200 524"><path d="M0 84 C 300 80 700 20 1000 40 C 1100 46 1160 60 1200 40 L1200 524 L0 524Z" fill="#212326"/></svg>
  <div class="brand" style="left:151px;top:4570px"><span class="brand-dot"></span>Brightline Coatings Co</div>
  <p class="abs footer-about">A family-run business providing premium design, fabrication and installation of powder coated aluminium, stainless steel and glass products across the Whitsundays, North Queensland.</p>
  <div class="fcol" style="left:511px"><h4>Our Services</h4><ul><li>Privacy Slat Screens</li><li>Glass Pool Fencing</li><li>Balustrades</li><li>Stainless Steel Handrails</li><li>Powder Coated Aluminium</li><li>Handrails</li><li>Electric Gates</li><li>Custom Fabrication</li><li>Professional Installation</li></ul></div>
  <div class="fcol" style="left:717px"><h4>Company</h4><ul><li>About Us</li><li>Privacy Screens</li><li>Balustrades</li><li>Glass Fencing</li><li>Stainless Steel Handrails</li><li>Aluminium Handrails</li><li>Pool Fencing</li><li>Gallery</li><li>Contact</li></ul></div>
  <div class="fcol" style="left:916px"><h4>Areas Serve</h4><ul><li>Whitsundays</li><li>Airlie Beach</li><li>Bowen</li><li>Ayr</li><li>Townsville</li></ul></div>
  <div class="abs contact-strip">
    <div class="contact-item"><span class="ic"><svg width="14" height="14" viewBox="0 0 24 24" fill="#fff"><path d="M12 2a7 7 0 0 0-7 7c0 5 7 13 7 13s7-8 7-13a7 7 0 0 0-7-7zm0 9.5A2.5 2.5 0 1 1 12 6.5a2.5 2.5 0 0 1 0 5z"/></svg></span><div><small>EMAIL:</small><b>hello@brightlinecoatings.com.au</b></div></div>
    <div class="contact-item"><span class="ic"><svg width="14" height="14" viewBox="0 0 24 24" fill="#fff"><path d="M6.6 10.8a15.1 15.1 0 0 0 6.6 6.6l2.2-2.2c.3-.3.7-.4 1-.2 1.1.4 2.3.6 3.6.6.6 0 1 .4 1 1V20c0 .6-.4 1-1 1A17 17 0 0 1 3 4c0-.6.4-1 1-1h3.5c.6 0 1 .4 1 1 0 1.3.2 2.5.6 3.6.1.3 0 .7-.2 1z"/></svg></span><div><small>PHONE:</small><b>+61 7 4900 1234</b></div></div>
    <div class="contact-item"><span class="ic"><svg width="14" height="14" viewBox="0 0 24 24" fill="#fff"><path d="M12 2a7 7 0 0 0-7 7c0 5 7 13 7 13s7-8 7-13a7 7 0 0 0-7-7zm0 9.5A2.5 2.5 0 1 1 12 6.5a2.5 2.5 0 0 1 0 5z"/></svg></span><div><small>ADDRESS:</small><b>WHITSUNDAYS, NORTH QUEENSLAND</b></div></div>
  </div>
  <a class="abs to-top"><svg width="10" height="10" viewBox="0 0 10 10"><path d="M5 8V2M2 5l3-3 3 3" stroke="#212326" stroke-width="1.4" fill="none"/></svg></a>
  <div class="abs footer-rule"></div>
  <div class="abs legal" style="left:151px">© 2026 Brightline Coatings Co. All rights reserved.</div>
  <div class="abs legal" style="left:720px;width:329px;text-align:right">Proudly serving Airlie Beach to Townsville | North Queensland</div>
</footer>

</body>
</html>
```